Hardcore nerd needs to stand out in a sea of dull Defence business cards

Wombarra Devices is a new Australian consulting engineering company that turns research and theory into practical systems. No evangelistic fluff, just mathematics and physics into electronic and optical circuits for consumer products, scientific research or Defence applications.

We already have a recognised logo (provided) which is often dark blue/black on a light background but we're open to other combinations. (Us engineers tend to have limited aesthetic imagination :)

Some of our recent products have included:
* Instrumentation for electrical testing,
* Radar jammers,
* GPS antenna design,
* Satellite tracking systems,
* High power lasers

We're open to both single and double-sided designs - happy to be convinced either way.

P.S. Another group is working on the web page, so - alas - our web site is currently of no use for images/ideas...

Target Market(s)

Engineering managers,
Scientists

Contact Information for Business Card

Dr Colin Harte
R&D Engineer

colin@wombarradevices.com.au
0427 563 710

PO Box XXX (to be confirmed)
Kelsby ACT 2917
Australia

Font styles to use
Serif
Sans Serif

Colors

Designer to choose colors to be used in the design.

Requirements
Must have
• My contact details!
• I've had many (great) "bold and plain" designs submitted already, so feel free to be artistically creative :)
• Happy to take advice re fonts/colours/printability etc.
Nice to have
• I'm not sure if "lists" are more at home on a CV than a business card, but representative services include:
• Applied electromagnetics
• RF and high speed electronics
• Signal and image processing
• Electro-optical and laser systems
• Concept-to-prototype design services
• If you're considering double sided cards, then often measuring/alignment grids/rulers feature on the back of similar cards.
• e.g. https://www.veltranoptics.example/newgrouppage9.cfm?objectgroup_id=4183
• https://www.veltranoptics.example/newgrouppage9.cfm?objectgroup_ID=4185
• ..or even a "Smith chart" (google will return lots)
• Generic images to represent a capability might work - googling images associated with keyword for each of these areas might help:
• - "passive radar", "phased array", "fdtd", "vircator"
• RF and high speed electronic design
• - "smith chart", "microstrip circuits", "dimensioned drawing", "electronic schematic"
• - "dft", "iir filter"
• - "optical cavity". "laser energy level diagram"
• Background/watermarked images outlines/wireframes/schematics would probably look OK.
Should not have
• If a list of projects/services is provided, it is important not to make the client feel that this is "all" the company can do. Engineering design is a creative discipline (like graphics :)
• Please, no stock "military" snaps like planes, missiles, etc!

```html
<!DOCTYPE html>
<html lang="en">
<head>
<meta charset="utf-8">
<title>Wombarra Devices – Business Card</title>
<link rel="stylesheet" href="https://fonts.googleapis.com/css2?family=Lato:wght@400;700;900&family=Arimo:wght@700&display=swap">
<style>
  :root {
    --stage: #5e5e5e;
    --card-light: #ededed;
    --navy: #0a2260;
    --navy-ink: #0b2a6b;
    --white: #ffffff;
    --rule: rgba(255, 255, 255, 0.55);
  }
  * { margin: 0; padding: 0; box-sizing: border-box; }
  html, body {
    width: 1200px; height: 900px; overflow: hidden;
    background: var(--stage);
  }
  .canvas { position: relative; width: 1200px; height: 900px; }

  .card {
    position: absolute; top: 235px;
    width: 416px; height: 416px; border-radius: 50%;
  }
  .card-front { left: 183px; background: var(--card-light); }
  .card-back  { left: 623px; background: var(--navy); color: var(--white); text-align: center; font-family: "Lato", sans-serif; }

  .brand {
    position: absolute; left: 62px; top: 155px;
    display: flex; align-items: center; gap: 14px;
  }
  .brand-dot {
    width: 96px; height: 96px; border-radius: 50%;
    background: var(--navy-ink);
  }
  .brand-name {
    font-family: "Lato", sans-serif; font-weight: 900;
    color: var(--navy-ink); font-size: 26px; line-height: 1.15;
    letter-spacing: 1px;
  }

  .holder-name {
    position: absolute; top: 80px; left: 0; right: 0;
    font-family: "Arimo", sans-serif; font-weight: 700; font-size: 22px;
  }
  .holder-role { position: absolute; top: 107px; left: 0; right: 0; font-size: 18px; }

  .contact-divider { position: absolute; top: 145px; left: 100px; width: 216px; height: 30px; }
  .contact-divider::before, .contact-divider::after {
    content: ""; position: absolute; top: 14px; width: 60px; height: 1px; background: var(--rule);
  }
  .contact-divider::before { left: 0; }
  .contact-divider::after { right: 0; }
  .contact-icons { display: flex; justify-content: center; gap: 4px; }
  .contact-icons svg { width: 28px; height: 28px; display: block; }

  .contact-lines { position: absolute; top: 182px; left: 0; right: 0; font-size: 19px; line-height: 25px; }
  .section-rule { position: absolute; top: 271px; left: 100px; width: 216px; height: 1px; background: var(--rule); }
  .postal { position: absolute; top: 285px; left: 0; right: 0; font-size: 19px; line-height: 24px; }
</style>
</head>
<body>
<main class="canvas">
  <section class="card card-front" aria-label="Card front">
    <div class="brand">
      <div class="brand-dot"></div>
      <div class="brand-name">WOMBARRA<br>DEVICES</div>
    </div>
  </section>

  <section class="card card-back" aria-label="Card back">
    <p class="holder-name">DR COLIN HARTE</p>
    <p class="holder-role">R&amp;D Engineer</p>

    <div class="contact-divider">
      <div class="contact-icons">
        <svg viewBox="0 0 28 28" aria-label="Phone">
          <circle cx="14" cy="14" r="13" fill="#fff"/>
          <path d="M7 12c0-3 14-3 14 0v2h-4v-2h-6v2H7z M9 15h10l1 6H8z" fill="#0a2260"/>
        </svg>
        <svg viewBox="0 0 28 28" aria-label="Email">
          <circle cx="14" cy="14" r="13" fill="#fff"/>
          <rect x="7" y="9" width="14" height="10" fill="none" stroke="#0a2260" stroke-width="1.8"/>
          <path d="M7 9l7 6 7-6" fill="none" stroke="#0a2260" stroke-width="1.8"/>
        </svg>
        <svg viewBox="0 0 28 28" aria-label="Web">
          <circle cx="14" cy="14" r="13" fill="#fff"/>
          <circle cx="14" cy="14" r="7" fill="none" stroke="#0a2260" stroke-width="1.8"/>
          <path d="M7 14h14M14 7c-3 4-3 10 0 14M14 7c3 4 3 10 0 14" fill="none" stroke="#0a2260" stroke-width="1.4"/>
        </svg>
      </div>
    </div>

    <p class="contact-lines">0427 563 710<br>colin@wombarradevices.com.au<br>www.wombarradevices.com.au</p>
    <div class="section-rule"></div>
    <p class="postal">PO Box XXX<br>Kelsby ACT 2917, Australia</p>
  </section>
</main>
</body>
</html>
```